I need an WORKROOM HAUS selling website

My WORKROOM HAUS store is driven by creativity and innovation. With this i am searching for an industry standard website for my WORKROOM HAUS and items selling website. I sell a wide range of WORKROOM HAUS items such as chairs, tables, burglary, cotton, wardrobe, etc. There will be a category for each of the items i sell. My business is based in the United States and services only US based residents. I don't accept online payments and customers are to pay on delivery of items. The website is to have images of the items i sell. I would like brown, black and golden colors because those are the colors furniture mostly make use of. Designs submitted should be unique.

Industry/Entity Type

Furniture Store

Coding

Coded - Design and coding required

```html
<!DOCTYPE html>
<html lang="en">
<head>
<meta charset="utf-8">
<title>Workroom Haus</title>
<link href="https://fonts.googleapis.com/css2?family=Open+Sans:wght@300;400;600;700&display=swap" rel="stylesheet">
<style>
  :root {
    --ink: #111111;
    --nav: #555555;
    --text-soft: #666666;
    --topbar: #f2f2f2;
    --rule: #dddddd;
    --footer: #000000;
    --footer-text: #d6d6d6;
    --footer-rule: #333333;
    --icon-disc: #5e5e5e;
    --social: #e6e6e6;
    --white: #ffffff;
    --hero-a: #eef3f4;
    --hero-b: #b9c9cc;
    --hero-c: #6f8083;
  }
  * { box-sizing: border-box; margin: 0; padding: 0; }
  html, body { width: 1142px; height: 1200px; overflow: hidden; }
  body { font-family: "Open Sans", Arial, sans-serif; color: var(--ink); background: var(--white); position: relative; }

  .topbar { height: 40px; background: var(--topbar); border-bottom: 1px solid var(--rule); display: flex; justify-content: flex-end; align-items: center; padding-right: 77px; }
  .topbar-phone { display: flex; align-items: center; gap: 7px; font-weight: 700; font-size: 19px; }

  .site-header { height: 99px; display: flex; align-items: center; justify-content: space-between; padding: 0 77px 0 76px; }
  .brand { font-weight: 300; font-size: 38px; letter-spacing: 1px; color: var(--ink); }
  .main-nav { display: flex; gap: 44px; }
  .main-nav a { text-decoration: none; color: var(--nav); font-weight: 300; font-size: 17px; }
  .main-nav a.is-active { color: var(--ink); font-weight: 400; }

  .hero { height: 546px; background: linear-gradient(100deg, var(--hero-a) 0%, #f7f9f9 30%, var(--hero-b) 55%, #dfe7e8 75%, var(--hero-c) 100%); }

  .welcome { text-align: center; padding-top: 58px; }
  .welcome h1 { font-weight: 300; font-size: 38px; letter-spacing: 0.5px; margin-bottom: 20px; }
  .welcome p { width: 830px; margin: 0 auto 24px; font-size: 14.5px; line-height: 24px; color: var(--text-soft); }

  .site-footer { position: absolute; left: 0; top: 991px; width: 1142px; height: 209px; background: var(--footer); color: var(--footer-text); padding: 0 73px; }
  .footer-top { display: flex; justify-content: space-between; align-items: center; height: 69px; border-bottom: 1px solid var(--footer-rule); }
  .footer-nav { display: flex; gap: 29px; padding-left: 2px; }
  .footer-nav a { text-decoration: none; color: var(--footer-text); font-size: 16px; }
  .social { display: flex; gap: 30px; padding-right: 2px; }
  .social span { width: 18px; height: 18px; border-radius: 50%; background: var(--social); display: block; }
  .footer-title { font-size: 20px; margin: 16px 0 17px 2px; color: var(--white); font-weight: 400; }
  .contact-row { display: flex; align-items: center; }
  .contact-item { display: flex; align-items: center; gap: 9px; font-size: 15px; line-height: 24px; }
  .contact-item:nth-child(1) { width: 260px; }
  .contact-item:nth-child(2) { width: 259px; }
  .contact-item:nth-child(3) { width: 262px; }
  .disc { width: 44px; height: 44px; border-radius: 50%; background: var(--icon-disc); display: flex; align-items: center; justify-content: center; flex: none; }
  .strong { font-weight: 600; color: var(--white); }
  .copyright { font-size: 15px; line-height: 24px; }
  .copyright b { color: var(--white); font-weight: 700; }
</style>
</head>
<body>
  <div class="topbar">
    <div class="topbar-phone">
      <svg width="20" height="20" viewBox="0 0 24 24"><path fill="#111" d="M6.6 10.8a15.1 15.1 0 0 0 6.6 6.6l2.2-2.2c.3-.3.7-.4 1-.2 1.1.4 2.300.6 3.6.6.6 0 1 .4 1 1V20c0 .6-.4 1-1 1A17 17 0 0 1 3 4c0-.6.4-1 1-1h3.5c.6 0 1 .4 1 1 0 1.3.2 2.5.6 3.6.1.3 0 .7-.2 1z"/></svg>
      555 014 2388
    </div>
  </div>

  <header class="site-header">
    <div class="brand">WORKROOM HAUS</div>
    <nav class="main-nav">
      <a href="#" class="is-active">HOME</a>
      <a href="#">ABOUT</a>
      <a href="#">PRODUCTS</a>
      <a href="#">SPECIALS</a>
      <a href="#">NEWS</a>
      <a href="#">CONTACT</a>
    </nav>
  </header>

  <div class="hero" role="img" aria-label="Bright modern office interior with a sculpted white wall, yellow lounge chairs and glass-walled workstations"></div>

  <section class="welcome">
    <h1>WELCOME TO WORKROOM HAUS</h1>
    <p>Lorem Ipsum is simply dummy text of the printing and typesetting industry. Lorem Ipsum has been the industry's standard dummy text ever since the 1500s, when an unknown printer took a galley of type and scrambled it to make a type specimen book.</p>
    <p>Lorem Ipsum is simply dummy text of the printing and typesetting industry. Lorem Ipsum has been the industry's standard dummy text ever since the 1500.</p>
  </section>

  <footer class="site-footer">
    <div class="footer-top">
      <nav class="footer-nav">
        <a href="#">Home</a><a href="#">About</a><a href="#">Products</a><a href="#">Specials</a><a href="#">News</a><a href="#">Contact</a>
      </nav>
      <div class="social" aria-label="Social links">
        <span role="img" aria-label="Social link"></span>
        <span role="img" aria-label="Social link"></span>
        <span role="img" aria-label="Social link"></span>
      </div>
    </div>
    <h2 class="footer-title">Contact Us</h2>
    <div class="contact-row">
      <div class="contact-item">
        <span class="disc"><svg width="16" height="20" viewBox="0 0 16 20"><path fill="#fff" d="M8 0a7 7 0 0 0-7 7c0 5 7 13 7 13s7-8 7-13a7 7 0 0 0-7-7zm0 9.5A2.5 2.5 0 1 1 8 4.5a2.5 2.5 0 0 1 0 5z"/></svg></span>
        <span>Lorem Ipsum is dummy<br>text of the printing.</span>
      </div>
      <div class="contact-item">
        <span class="disc"><svg width="20" height="20" viewBox="0 0 24 24"><path fill="#fff" d="M6.6 10.8a15.1 15.1 0 0 0 6.6 6.6l2.2-2.2c.3-.3.7-.4 1-.2 1.1.4 2.3.6 3.6.6.6 0 1 .4 1 1V20c0 .6-.4 1-1 1A17 17 0 0 1 3 4c0-.6.4-1 1-1h3.5c.6 0 1 .4 1 1 0 1.3.2 2.5.6 3.6.1.3 0 .7-.2 1z"/></svg></span>
        <span class="strong">555 014 2388</span>
      </div>
      <div class="contact-item">
        <span class="disc"><svg width="20" height="16" viewBox="0 0 20 16"><rect x="1" y="1" width="18" height="14" rx="2" fill="none" stroke="#fff" stroke-width="2"/><path d="M2 3l8 6 8-6" fill="none" stroke="#fff" stroke-width="2"/></svg></span>
        <span>hello@workroomhaus.com</span>
      </div>
      <div class="copyright">© <b>WORKROOM HAUS</b> - 2016.<br>All Rights Reserved.</div>
    </div>
  </footer>
</body>
</html>
```